FinTech company looking to revamp and expand client-facing interface for our financial models

Pellworth Engines currently has a very simple website that allows clients to interact with our financial models. We are looking to completely redesign the current site and add several extra pages to provide extra functionality. We want the design to have a modern, slick feel, that will work on both a desktop or a tablet. It should be straightforward for clients to move between different pages at any time, and clear from the layout how to interact with the more advanced features. We have included screenshots of existing pages in the attached design brief, as well as sketches of the functionality required by the new pages, but can't provide a direct link to the current site.
Target Market(s)
Professional investors that will be paying to access the interface
Industry/Entity Type
Finance
Number of Pages Required
4 page
Colors
Designer to choose colors to be used in the design.
Look and feel
Each slider illustrates characteristics of the customer's brand and the style your logo design should communicate.

```html
<!DOCTYPE html>
<html lang="en">
<head>
<meta charset="utf-8">
<title>Backtest – Pellworth Engines</title>
<link rel="stylesheet" href="https://fonts.googleapis.com/css2?family=Montserrat:wght@500;600;700&family=Open+Sans:wght@600;700&family=Roboto+Condensed:wght@400&family=Roboto:wght@400&display=swap">
<style>
  :root{
    --page:#e6e6e6;
    --panel:#f2f2f2;
    --white:#ffffff;
    --ink:#111111;
    --dark:#1a1a1a;
    --navy:#0d3268;
    --teal:#0a6b68;
    --row-alt:#efefef;
    --grid:#dcdcdc;
    --axis:#9a9a9a;
    --line:#6fa3a0;
  }
  *{box-sizing:border-box;margin:0;padding:0}
  html,body{width:1169px;height:1200px;overflow:hidden;background:var(--page)}
  body{position:relative;font-family:"Open Sans",sans-serif;color:var(--ink)}
  .frame{position:absolute;left:13px;top:13px;width:1142px;height:1174px;
    background:linear-gradient(#e4e4e4,#f6f6f6 30%,#f6f6f6)}
  .topbar{position:absolute;left:0;top:0;width:1142px;height:54px;background:var(--white);
    box-shadow:0 3px 8px rgba(0,0,0,.08);display:flex;font-weight:700;font-size:13px}
  .brand{width:162px;display:flex;align-items:center;justify-content:center;font-size:17px;border-right:1px solid #e6e6e6}
  .tab{width:81px;display:flex;align-items:center;justify-content:center;border-right:1px solid #e6e6e6}
  .spacer{flex:1;border-right:1px solid #e6e6e6}
  .navlink{display:flex;align-items:center;justify-content:center;gap:7px;font-size:12px;border-right:1px solid #e6e6e6}
  .navlink:last-child{border-right:none}
  .navlink svg{width:22px;height:22px}
  .title-btn{position:absolute;left:425px;top:90px;width:292px;height:50px;background:var(--navy);color:var(--white);
    border-radius:3px;display:flex;align-items:center;justify-content:center;font-family:"Montserrat",sans-serif;font-weight:600;font-size:19px}
  .chart-card{position:absolute;left:81px;top:158px;width:1043px;height:404px;background:var(--white);border-radius:3px;box-shadow:0 1px 4px rgba(0,0,0,.06)}
  .chart-card svg{width:100%;height:100%;display:block}
  .axis-label{font-family:"Roboto",sans-serif;font-size:13px;fill:#333}
  .model-tab{position:absolute;left:0;top:306px;width:45px;height:225px;background:var(--dark);border-radius:0 4px 4px 0}
  .model-tab span{position:absolute;left:50%;top:50%;transform:translate(-50%,-50%) rotate(-90deg);white-space:nowrap;
    color:var(--white);font-family:"Montserrat",sans-serif;font-weight:600;font-size:15px;letter-spacing:.5px}
  .model-tab .toggle{position:absolute;left:34px;top:101px;width:24px;height:24px;border-radius:50%;background:var(--navy);border:2px solid var(--white)}
  .toggle svg{width:20px;height:20px;display:block}
  table{position:absolute;border-collapse:collapse;background:var(--white);box-shadow:0 2px 6px rgba(0,0,0,.08);table-layout:fixed}
  th{height:63px;background:var(--dark);color:var(--white);font-family:"Montserrat",sans-serif;font-weight:600;font-size:15px;border-left:1px solid #333}
  th:first-child{border-left:none}
  thead tr th:first-child{border-top-left-radius:4px}
  thead tr th:last-child{border-top-right-radius:4px}
  td{height:62px;text-align:center;font-family:"Roboto Condensed",sans-serif;font-size:16px;border-left:1px solid #eaeaea}
  td:first-child{border-left:none}
  tbody tr:nth-child(even) td{background:var(--row-alt)}
  .stats-table{left:81px;top:607px;width:360px}
  .trades-table{left:477px;top:607px;width:647px}
  .load-more{position:absolute;top:1066px;width:180px;height:36px;background:var(--teal);color:var(--white);border-radius:3px;
    display:flex;align-items:center;justify-content:center;gap:10px;font-family:"Open Sans",sans-serif;font-weight:700;font-size:12.5px}
  .load-more svg{width:20px;height:20px}
</style>
</head>
<body>
<div class="frame">
  <header class="topbar">
    <div class="brand">VORTA</div>
    <div class="tab">250D</div>
    <div class="tab">83D</div>
    <div class="tab">42D</div>
    <div class="spacer"></div>
    <div class="navlink" style="width:126px">
      <svg viewBox="0 0 24 24" fill="none" stroke="#111" stroke-width="2"><path d="M3 11 12 3l9 8"/><path d="M5 10v10h5v-6h4v6h5V10"/></svg>MODELS</div>
    <div class="navlink" style="width:160px">
      <svg viewBox="0 0 24 24" fill="none" stroke="#111" stroke-width="1.6"><circle cx="12" cy="12" r="3"/><circle cx="12" cy="12" r="7" stroke-dasharray="2 2"/><path d="M12 1v3M12 20v3M1 12h3M20 12h3M4.2 4.2l2 2M17.8 17.8l2 2M4.2 19.8l2-2M17.8 6.2l2-2"/></svg>SENSITIVITIES</div>
    <div class="navlink" style="width:177px">
      <svg viewBox="0 0 24 24" fill="none" stroke="#111" stroke-width="1.8"><path d="M12 2.5l2.9 6.2 6.6.7-5 4.5 1.4 6.6L12 17.2 6.1 20.5l1.4-6.6-5-4.5 6.6-.7z"/></svg>FAVOURITES</div>
  </header>

  <div class="title-btn">BACKTEST PAGE</div>

  <section class="chart-card">
    <svg viewBox="0 0 1160 450" preserveAspectRatio="none">
      <g stroke="var(--grid)" stroke-width="1">
        <line x1="81" y1="105" x2="1091" y2="105"/><line x1="81" y1="182.6" x2="1091" y2="182.6"/>
        <line x1="81" y1="260.3" x2="1091" y2="260.3"/><line x1="81" y1="338" x2="1091" y2="338"/>
        <line x1="143" y1="75" x2="143" y2="366"/><line x1="231" y1="75" x2="231" y2="366"/>
        <line x1="316" y1="75" x2="316" y2="366"/><line x1="404" y1="75" x2="404" y2="366"/>
        <line x1="489" y1="75" x2="489" y2="366"/><line x1="577" y1="75" x2="577" y2="366"/>
        <line x1="665" y1="75" x2="665" y2="366"/><line x1="744" y1="75" x2="744" y2="366"/>
        <line x1="832" y1="75" x2="832" y2="366"/><line x1="917" y1="75" x2="917" y2="366"/>
        <line x1="1005" y1="75" x2="1005" y2="366"/><line x1="1091" y1="75" x2="1091" y2="366"/>
      </g>
      <g stroke="var(--axis)" stroke-width="1.3"><line x1="81" y1="75" x2="81" y2="366"/><line x1="81" y1="366" x2="1091" y2="366"/></g>
      <g class="axis-label" text-anchor="end">
        <text x="78" y="110">30</text><text x="78" y="187">25</text><text x="78" y="265">20</text><text x="78" y="343">15</text>
      </g>
      <g class="axis-label" text-anchor="middle">
        <text x="141" y="72">Aug 2018</text><text x="228" y="72">Sep 2018</text><text x="313" y="72">Oct 2018</text>
        <text x="401" y="72">Nov 2018</text><text x="486" y="72">Dec 2018</text><text x="573" y="72">Jan 2019</text>
        <text x="661" y="72">Feb 2019</text><text x="740" y="72">Mar 2019</text><text x="828" y="72">Apr 2019</text>
        <text x="913" y="72">May 2019</text><text x="1000" y="72">Jun 2019</text><text x="1071" y="72">Jul 2019</text>
        <text x="143" y="384">Aug 2018</text><text x="231" y="384">Sep 2018</text><text x="316" y="384">Oct 2018</text>
        <text x="404" y="384">Nov 2018</text><text x="489" y="384">Dec 2018</text><text x="577" y="384">Jan 2019</text>
        <text x="665" y="384">Feb 2019</text><text x="744" y="384">Mar 2019</text><text x="832" y="384">Apr 2019</text>
        <text x="917" y="384">May 2019</text><text x="1005" y="384">Jun 2019</text><text x="1072" y="384">Jul 2019</text>
      </g>
      <g transform="matrix(1 0 0 -15.53 -105 570.9)">
        <polyline fill="none" stroke="var(--line)" stroke-width="1.4" vector-effect="non-scaling-stroke" points="186,21.5 192,21.2 200,21 208,21 212,17.5 222,17.6 228,19.2 236,19.3 246,19.5 248,20 262,20 266,19.2 270,19.3 274,16.5 282,16.6 287,20 300,20 306,19.8 312,20.7 320,20.6 330,20.7 334,20 342,20.2 348,19 356,18.8 366,19 372,18.7 380,18.8 386,18.5 394,19 400,18.8 404,17.3 410,16.3 418,16.4 424,16 430,16.3 436,15.8 442,16.2 446,17 452,16.6 462,16.2 468,15.5 474,15.3 480,15 484,14.6 486,15.2 500,15.3 504,17 508,19.1 514,19.3 520,19.3 524,19.7 530,20.5 538,20.7 542,17.4 548,17.8 556,17.6 560,17.9 566,17.6 578,17.6 582,18.9 586,19.1 592,17.6 598,17.5 604,18.8 614,19.2 622,19.5 628,19.9 636,20.1 642,20.3 646,22.2 650,22.8 660,23 668,23 672,22.3 680,22.3 686,21.9 690,23.5 696,24 702,24.2 706,25.2 712,25.1 718,25.4 724,25.6 730,25.8 738,25.9 744,26.2 750,27.8 756,26.7 760,27 764,27.4 768,25 772,24.6 776,25.1 780,24.5 786,25.3 790,26 794,26.4 798,25.5 802,24 806,24.6 814,24.7 820,25 824,27.3 830,26.5 836,26.7 842,26.3 850,26.6 858,26.6 864,28.6 870,28.8 876,29 882,29.3 888,29 894,28.8 898,26.3 904,26.8 912,26.5 920,26.8 926,26.4 932,27 936,26.5 940,28.7 944,27.8 948,27 956,26.9 964,26.6 968,25 978,25 982,27 988,26.5 994,27 1000,26.4 1006,27.2 1012,26.9 1020,26.8 1026,26.6 1030,27.3 1036,27.4 1042,27.3 1046,26.8 1054,26.8 1062,27 1072,27.1 1080,26.9 1086,27.3 1092,26.7 1100,27.1 1106,26.7 1112,27.2 1118,27.5 1122,27.8 1130,27.6 1136,27.3 1146,27.1 1154,27.3 1158,28 1162,29 1170,29.2 1176,29.6 1182,29 1188,29.2 1192,29 1196,30.2"/>
      </g>
    </svg>
  </section>

  <aside class="model-tab">
    <span>SELECT A MODEL</span>
    <div class="toggle"><svg viewBox="0 0 20 20" fill="none" stroke="#fff" stroke-width="2"><path d="M5 10h10M11 6l4 4-4 4"/></svg></div>
  </aside>

  <table class="stats-table">
    <thead><tr><th colspan="2">Stats</th></tr></thead>
    <tbody>
      <tr><td>Stat 1</td><td>0.5</td></tr>
      <tr><td>Stat 2</td><td>-3</td></tr>
      <tr><td>Stat 3</td><td>30%</td></tr>
      <tr><td>Stat 4</td><td>0.5</td></tr>
      <tr><td>Stat 5</td><td>-3</td></tr>
      <tr><td>Stat 6</td><td>30%</td></tr>
    </tbody>
  </table>

  <table class="trades-table">
    <thead><tr><th>Open</th><th>Close</th><th>Size</th><th>Return</th></tr></thead>
    <tbody>
      <tr><td>2018-04-05</td><td>2018-04-07</td><td>13</td><td>5%</td></tr>
      <tr><td>2018-04-05</td><td>2018-04-07</td><td>12</td><td>7%</td></tr>
      <tr><td>2018-04-05</td><td>2018-04-07</td><td>15</td><td>6%</td></tr>
      <tr><td>2018-04-05</td><td>2018-04-07</td><td>16</td><td>9%</td></tr>
      <tr><td>2018-04-05</td><td>2018-04-07</td><td>12</td><td>8%</td></tr>
      <tr><td>2018-04-05</td><td>2018-04-07</td><td>19</td><td>6%</td></tr>
    </tbody>
  </table>

  <div class="load-more" style="left:171px">
    <svg viewBox="0 0 20 20" fill="none" stroke="#fff" stroke-width="1.8"><path d="M10 3v10M6 9l4 4 4-4M3 14v3h14v-3"/></svg>LOAD MORE</div>
  <div class="load-more" style="left:711px">
    <svg viewBox="0 0 20 20" fill="none" stroke="#fff" stroke-width="1.8"><path d="M10 3v10M6 9l4 4 4-4M3 14v3h14v-3"/></svg>LOAD MORE</div>
</div>
</body>
</html>
```